High-end construction company needs a business card design

We need a modern looking business card that draws people in, is memorable and looks so good people will want to sick it on their fridges.
On the first side what is needed are:
Logo
My name - Tomasz Brelwik
Title - Managing Director
Website - www.varkelt.co.uk
Email - tomasz@varkelt.co.uk
Telephone - 020 5194 6281
Mobile - 07845139072
On the back side was is needed is a list of all the services we provide:
-Kitchen Renovations
-Bathroom Renovations
-House Renovations
-Garage Conversions
-Extensions
-Loft Conversions
-Conservatories
-Carpentry
-Tiling
-Electrical
-Plumbing & Heating
-Bricklaying
-Landscaping
-Decorating
-Plastering
We would like the colours to be the same shades as on the logo with grey or black for the words.
Target Market(s)
Anyone who needs building work done
Contact Information for Business Card
This business card is for a construction company which strives to deliver excellent service and quality.
The look and feel of the card should represent this.
Requirements
Must have
- On the first side what is needed are:
Logo
My name - Tomasz Brelwik
Title - Managing Director
Website - www.varkelt.co.uk
Email - tomasz@varkelt.co.uk
Telephone - 020 5194 6281
Mobile - 07845139072
Nice to have
- Cool looking features

```html
<!DOCTYPE html>
<html lang="en">
<head>
<meta charset="utf-8">
<title>Varkelt Construction Ltd — Business Card</title>
<link rel="stylesheet" href="https://fonts.googleapis.com/css2?family=Montserrat:wght@400;500;600&family=Oswald:wght@500&display=swap">
<style>
  :root {
    --backdrop: #d4d5d0;
    --card-white: #f1f1f0;
    --brand-green: #4a8c3f;
    --accent-green: #6bbf3a;
    --edge-green: #7cc24f;
    --text-grey: #4a4a4a;
    --text-white: #ffffff;
  }
  * { box-sizing: border-box; margin: 0; padding: 0; }
  html, body {
    width: 1200px; height: 1058px; overflow: hidden;
    background: var(--backdrop);
  }
  .sheet {
    width: 1200px; height: 1058px;
    display: flex; flex-direction: column; align-items: center; justify-content: center;
    gap: 56px;
  }
  .card {
    position: relative;
    width: 760px; height: 440px;
    border-bottom: 5px solid var(--edge-green);
    box-shadow: 0 12px 28px rgba(0,0,0,0.18);
  }
  /* Front */
  .card--front { background: var(--card-white); font-family: "Montserrat", sans-serif; color: var(--text-grey); }
  .identity { position: absolute; left: 70px; top: 150px; width: 290px; text-align: right; }
  .identity__name {
    font-family: "Oswald", sans-serif; font-weight: 500;
    font-size: 44px; letter-spacing: 1px; text-transform: uppercase;
    color: var(--accent-green); line-height: 1.1;
  }
  .identity__title { font-size: 20px; font-weight: 400; margin-top: 4px; }
  .divider { position: absolute; left: 392px; top: 130px; width: 2px; height: 110px; background: var(--accent-green); }
  .contacts { position: absolute; left: 428px; top: 120px; list-style: none; font-size: 19px; line-height: 32px; }
  .contacts li { display: flex; align-items: center; gap: 10px; }
  .contacts svg { width: 16px; height: 16px; flex: none; }
  .address { position: absolute; right: 60px; bottom: 44px; font-size: 19px; }
  /* Back */
  .card--back {
    background: var(--brand-green); color: var(--text-white);
    font-family: "Montserrat", sans-serif;
    display: flex; flex-direction: column; align-items: center; justify-content: center;
  }
  .wordmark { display: flex; align-items: center; gap: 14px; font-weight: 600; font-size: 36px; letter-spacing: 2px; text-transform: uppercase; }
  .wordmark__mark { width: 22px; height: 22px; background: var(--text-white); }
  .services { margin-top: 48px; text-align: center; font-size: 19px; line-height: 30px; font-weight: 400; letter-spacing: 0.3px; }
</style>
</head>
<body>
<main class="sheet">
  <section class="card card--front" aria-label="Front of business card">
    <div class="identity">
      <h1 class="identity__name">Tomasz Brelwik</h1>
      <p class="identity__title">Managing Director</p>
    </div>
    <div class="divider"></div>
    <ul class="contacts">
      <li>
        <svg viewBox="0 0 16 16"><path d="M4 2l2.5 3-1.5 1.5c.8 1.8 2.4 3.4 4.5 4.5L11 9.5l3 2.5-1.5 2.5C7 14 2 9 1.5 3.5z" fill="var(--accent-green)"/></svg>
        020 5194 6281
      </li>
      <li>
        <svg viewBox="0 0 16 16"><rect x="4" y="1.5" width="8" height="13" rx="1.5" fill="none" stroke="var(--accent-green)" stroke-width="1.6"/><circle cx="8" cy="12" r="1" fill="var(--accent-green)"/></svg>
        07845139072
      </li>
      <li>
        <svg viewBox="0 0 16 16"><rect x="1.5" y="3.5" width="13" height="9" fill="none" stroke="var(--accent-green)" stroke-width="1.6"/><path d="M1.5 3.5L8 9l6.5-5.5" fill="none" stroke="var(--accent-green)" stroke-width="1.6"/></svg>
        tomasz@varkelt.co.uk
      </li>
      <li>
        <svg viewBox="0 0 16 16"><circle cx="8" cy="8" r="6.5" fill="none" stroke="var(--accent-green)" stroke-width="1.5"/><ellipse cx="8" cy="8" rx="2.8" ry="6.5" fill="none" stroke="var(--accent-green)" stroke-width="1.2"/><path d="M1.5 8h13" stroke="var(--accent-green)" stroke-width="1.2"/></svg>
        www.varkelt.co.uk
      </li>
    </ul>
    <p class="address">14-16 Harwell Street, London, N4 2QT</p>
  </section>

  <section class="card card--back" aria-label="Back of business card">
    <div class="wordmark">
      <span class="wordmark__mark"></span>
      <span>Varkelt Construction Ltd</span>
    </div>
    <p class="services">
      Kitchen Renovations | Bathroom Renovations<br>
      House Renovations | Garage Conversions | Extensions<br>
      Loft Conversions | Conservatories | Carpentry | Tiling | Electrical<br>
      Plumbing &amp; Heating | Bricklaying | Landscaping | Decorating | Plastering
    </p>
  </section>
</main>
</body>
</html>
```